CV Template

We need a graphic design to our new CV templates for our consultants. We are a small young Danish upcoming IT-business company making software solutions for our customers etc. You can visit our new website here: dev.sol-brovaerk.com, then you can see our web design, colors etc. I have attached a file for your inspiration :-) In the presentation I would like to have a picture of the employee, some text who descripe the profile/consultant and then I imagine that there is a table where we can write the employee's skills etc.

I would like the design to be "fresh & catchy" :-)

Looking forward to hear from you.

Best regards,
Hanne

```html
<!DOCTYPE html>
<html lang="da">
<head>
<meta charset="utf-8">
<title>CV – Jonas Albrechtsen</title>
<link href="https://fonts.googleapis.com/css2?family=Open+Sans:wght@400;600;700&family=Source+Sans+3:wght@400;700&family=Cormorant+Garamond:wght@500&display=swap" rel="stylesheet">
<style>
  :root{
    --page:#eef1f7;
    --card:#ffffff;
    --accent:#14c8f0;
    --marker:#f5b800;
    --ink:#111111;
    --body:#555a60;
    --brand:#4a5a78;
  }
  *{margin:0;padding:0;box-sizing:border-box}
  html,body{width:902px;height:1200px;overflow:hidden;background:var(--page)}
  .canvas{position:relative;width:902px;height:1200px;background:var(--page);font-family:"Open Sans",Arial,sans-serif;color:var(--body)}
  .brand{position:absolute;left:646px;top:66px;font-family:"Cormorant Garamond",Georgia,serif;font-weight:500;font-size:22px;letter-spacing:1px;color:var(--brand)}
  .portrait{position:absolute;left:160px;top:104px;width:215px;height:215px;border-radius:50%;background:radial-gradient(circle at 50% 40%,#c9a58f 0%,#a0876f 35%,#7d8474 70%,#d9dcdc 100%)}
  .card{position:absolute;left:55px;top:276px;width:795px;height:792px;background:var(--card);border-radius:52px}
  .name{position:absolute;left:419px;top:152px;font-family:"Source Sans 3",Arial,sans-serif;font-weight:700;font-size:38px;color:var(--ink);letter-spacing:-0.3px}
  .title{position:absolute;left:419px;top:201px;font-family:"Source Sans 3",Arial,sans-serif;font-size:22px;line-height:30px;color:var(--ink)}
  .side{position:absolute;left:115px;width:242px;text-align:right}
  .heading{font-weight:700;font-size:18px;color:var(--accent);padding-bottom:2px;border-bottom:1px solid var(--accent);margin-bottom:6px}
  .side p{font-size:13.3px;line-height:20.6px;margin-left:14px}
  .side p + p{margin-top:8px}
  .divider{position:absolute;left:387px;top:308px;width:2px;height:728px;background:var(--accent)}
  .main{position:absolute;left:422px;top:314px;width:362px}
  .main .heading{text-align:left}
  .main .intro{font-size:13.3px;line-height:20.6px}
  .colon{color:var(--accent);font-weight:700}
  .subheading{margin-top:20px;font-size:13px;font-weight:700;color:var(--accent)}
  .projects{list-style:none;margin-top:16px;width:340px}
  .project{position:relative;padding-left:21px;font-size:13.3px;line-height:19px;color:var(--ink);margin-bottom:19px}
  .project b{position:absolute;left:3px;top:0;color:var(--marker);font-weight:700}
  .footer{position:absolute;top:1089px;left:0;width:902px;font-size:12px;font-weight:600;color:var(--ink)}
  .footer span{position:absolute;white-space:nowrap}
</style>
</head>
<body>
<div class="canvas">
  <div class="brand">Sol Brovaerk</div>
  <div class="portrait" role="img" aria-label="Portrætfoto af konsulenten"></div>
  <div class="card"></div>

  <h1 class="name">JONAS ALBRECHTSEN</h1>
  <div class="title">Rutineret og erfaren<br>Software udvikler &amp; konsulent</div>

  <section class="side" style="top:314px">
    <h2 class="heading">Profilbeskrivelse</h2>
    <p>Erfaren software udvikler med 25 års erfaring, som selvstændig hvor han bl.a. har arbejdet med udvikling af kundespecifikke applikationer til NS til WEB i samarbejde med kunder/ brugere. Derudover stor erfaring med analyse, design, programmering, test, uddannelse/ undervisning, kundesupport og projektledelse. Ud over at være en dygtig software udvikler er han også en stabil og rutineret konsulent, som er vant til, at yde konsulentbistand, support og udvikling af softwareløsninger til NS, Fjordix og WEB.</p>
  </section>

  <section class="side" style="top:680px">
    <h2 class="heading">Uddannelse</h2>
    <p>Uddannet som datalog/cand. scient ved Øresund Universitet februar 1989, hovedfag datalogi, bifag matematik</p>
  </section>

  <section class="side" style="top:822px">
    <h2 class="heading">Certificeringer</h2>
    <p>Ingen certificeringer</p>
  </section>

  <section class="side" style="top:903px">
    <h2 class="heading">Sprog</h2>
    <p>Dansk: Modersmål i både tale- og skrift</p>
    <p>Engelsk: Behersker det i både tale- og skrift</p>
  </section>

  <div class="divider"></div>

  <section class="main">
    <h2 class="heading">Erhvervs erfaringer</h2>
    <p class="intro">Været selvstændig i 25 år med egen virksomhed hvor forretningsområdet primært bestod i udvikling af kundespecifikke applikationer til NS, Fjordix og WEB primært baseret på Klar Basis, VSK, Kava, SSP, NSDB, MinDB, Orakul, NS Arkiv, Paradig.<span class="colon">:</span></p>
    <h3 class="subheading">Eksempler på udviklingsprojekter</h3>
    <ul class="projects">
      <li class="project"><b>A</b>WEB-baseret pakkelistesystem til Nordkran Industri med mulighed for leverandørregistreringer og opfølgning (shipping/ expediting) hos Nordkran Industri. Tilsvarende system udviklet til Kalvø Katalyse.</li>
      <li class="project"><b>B</b>Kørselsregistreringssystem udviklet i Klar Basis som Rammevis-applikation til Nordvagt Logistik.</li>
      <li class="project"><b>C</b>Beregnings- og administrationsprogrammer til Brevduelauget Norden (i dag også anvendt i Sverige og Norge), dels som Rammevis-applikationer, dels WEB på Fjordix-server.</li>
    </ul>
  </section>

  <footer class="footer">
    <span style="left:91px">Sol Brovaerk ApS</span>
    <span style="left:210px">Lyngbakken 14</span>
    <span style="left:311px">2300 København S.</span>
    <span style="left:452px">Tel: +45 20 31 47 58</span>
    <span style="left:598px">www.sol-brovaerk.dk</span>
  </footer>
</div>
</body>
</html>
```